Solution Matrix for our Company

Develop an image that describes our "4 solutions". We eventually will list the products and services we have that address the solution being discussed. Our main website is http://brightlanework.com/. Feel free to look through the material there as well as the material we are addressing.

The mock document is a summary of the 4 solution buckets. We have also attached some samples from states that have done similar work. Feel free to be creative and use graphics and/or pictures in your design

Target Market(s)

Education

```html
<!DOCTYPE html>
<html lang="en">
<head>
<meta charset="utf-8">
<title>BLW Career Readiness Model</title>
<link rel="stylesheet" href="https://fonts.googleapis.com/css2?family=Montserrat:wght@300;400;800;900&family=Roboto+Condensed:wght@400;700&display=swap">
<style>
  :root{
    --page:#fbfbfb;
    --ink:#1b1b1b;
    --orange:#f5921f;
    --orange-deep:#ee8a1c;
    --header-dark:#2f2f2f;
    --header-mid:#5a5a5a;
    --supported:#b8ec68;
    --wise:#7fd3b6;
    --engaged:#e2472f;
    --prepared:#ee8944;
    --panel-supported:#eef8df;
    --panel-wise:#e2f3ee;
    --panel-engaged:#f6dad5;
    --panel-prepared:#fce8d7;
    --ring-grey:#8a8a8a;
    --hub-ring:#65767f;
    --white:#ffffff;
  }
  *{margin:0;padding:0;box-sizing:border-box}
  html,body{width:1200px;height:899px;overflow:hidden;background:var(--page)}
  .canvas{position:relative;width:1200px;height:899px;font-family:"Roboto Condensed",sans-serif;color:var(--ink)}

  .header-band{position:absolute;left:69px;top:38px;width:830px;height:88px}
  .header-title{position:absolute;left:108px;top:56px;font-family:"Montserrat",sans-serif;font-size:41px;line-height:52px;color:var(--white);letter-spacing:0.5px;white-space:nowrap}
  .header-title .light{font-weight:400}
  .header-title .heavy{font-weight:900}

  .brand{position:absolute;left:915px;top:86px;display:flex;align-items:center;gap:7px}
  .brand-dot{width:16px;height:16px;border-radius:50%;background:var(--orange)}
  .brand-name{font-family:"Roboto Condensed",sans-serif;font-weight:700;font-size:19px;color:var(--orange);letter-spacing:0.4px}

  .rule{position:absolute;left:69px;width:1063px;background:var(--orange)}
  .rule-top{top:133px;height:6px}
  .rule-bottom{top:854px;height:5px}

  .panel{position:absolute}
  .panel-supported{left:69px;top:144px;width:531px;height:368px;background:var(--panel-supported)}
  .panel-wise{left:600px;top:144px;width:532px;height:368px;background:var(--panel-wise)}
  .panel-engaged{left:69px;top:512px;width:531px;height:342px;background:var(--panel-engaged)}
  .panel-prepared{left:600px;top:512px;width:532px;height:342px;background:var(--panel-prepared)}

  .divider-v{position:absolute;left:599px;top:144px;width:0;height:710px;border-left:3px dashed var(--white)}
  .divider-h{position:absolute;left:69px;top:510px;width:1063px;height:0;border-top:3px dashed var(--white)}

  .mission{position:absolute;left:322px;top:139px;width:557px;height:51px;background:var(--orange);border-radius:0 0 10px 10px;color:var(--white);font-family:"Roboto Condensed",sans-serif;font-weight:700;font-size:23px;text-align:center;line-height:50px;letter-spacing:0.2px}

  .icon-badge{position:absolute;width:98px;height:98px}
  .badge-supported{left:112px;top:152px}
  .badge-wise{left:991px;top:152px}
  .badge-engaged{left:112px;top:545px}
  .badge-prepared{left:989px;top:546px}

  .copy{position:absolute;font-size:17.5px;line-height:21px;white-space:nowrap}
  .copy p{margin-bottom:21px}
  .copy ul{list-style:none}
  .copy li{position:relative}
  .copy-left li{padding-left:12px}
  .copy-left li::before{content:"•";position:absolute;left:0}
  .copy-right{text-align:right}
  .copy-right li::before{content:"• "}
  .copy-right li.note::before{content:none}
  .copy-supported{left:112px;top:259px}
  .copy-wise{right:113px;top:259px}
  .copy-engaged{left:112px;top:651px}
  .copy-prepared{right:113px;top:651px}

  .wheel{position:absolute;left:0;top:0;width:1200px;height:899px}
  .ring-label{font-family:"Roboto Condensed",sans-serif;font-weight:700;font-size:27px;fill:var(--white);letter-spacing:1px}

  .hub{position:absolute;left:474px;top:402px;width:252px;text-align:center}
  .hub-heading{color:var(--orange-deep);font-weight:700;font-size:16.5px;line-height:19px}
  .hub-body{font-size:13px;line-height:16px;margin-top:3px}
  .hub-rule{width:224px;height:2px;background:var(--orange);margin:9px auto 9px}
  .hub-tools{list-style:none;font-size:13px;line-height:16px;margin-top:4px}
  .hub-tools li::before{content:"•";color:var(--orange);margin-right:5px}
</style>
</head>
<body>
<main class="canvas">

  <svg class="header-band" viewBox="0 0 830 88" aria-hidden="true">
    <defs>
      <linearGradient id="headerShade" x1="0" x2="1" y1="0" y2="0">
        <stop offset="0" stop-color="var(--header-dark)"/>
        <stop offset="0.55" stop-color="var(--header-mid)"/>
        <stop offset="1" stop-color="var(--header-dark)"/>
      </linearGradient>
    </defs>
    <polygon points="0,0 830,0 781,88 0,88" fill="url(#headerShade)"/>
  </svg>
  <h1 class="header-title"><span class="light">BLW </span><span class="heavy">CAREER READINESS</span><span class="light"> MODEL</span></h1>

  <div class="brand">
    <span class="brand-dot"></span>
    <span class="brand-name">BRIGHTLANE WORK</span>
  </div>

  <div class="rule rule-top"></div>

  <section class="panel panel-supported"></section>
  <section class="panel panel-wise"></section>
  <section class="panel panel-engaged"></section>
  <section class="panel panel-prepared"></section>
  <div class="divider-v"></div>
  <div class="divider-h"></div>

  <div class="mission">OUR MISSION IS TO ENSURE ALL STUDENTS ARE</div>

  <svg class="icon-badge badge-supported" viewBox="0 0 98 98" role="img" aria-label="Icon of an open hand holding a gear">
    <circle cx="49" cy="49" r="49" fill="#b5ec66"/>
    <circle cx="49" cy="49" r="38" fill="#8fcf3e"/>
    <circle cx="49" cy="49" r="31" fill="#7cbd34"/>
  </svg>
  <svg class="icon-badge badge-wise" viewBox="0 0 98 98" role="img" aria-label="Icon of a ladder rising to a cloud">
    <circle cx="49" cy="49" r="49" fill="#7fd3b6"/>
    <circle cx="49" cy="49" r="38" fill="#16a77c"/>
    <circle cx="49" cy="49" r="31" fill="#0d9a6f"/>
  </svg>
  <svg class="icon-badge badge-engaged" viewBox="0 0 98 98" role="img" aria-label="Icon of a gear with a wrench">
    <circle cx="49" cy="49" r="49" fill="#d24a37"/>
    <circle cx="49" cy="49" r="38" fill="#b42a1b"/>
    <circle cx="49" cy="49" r="31" fill="#a91f12"/>
  </svg>
  <svg class="icon-badge badge-prepared" viewBox="0 0 98 98" role="img" aria-label="Icon of a climber planting a flag on a summit">
    <circle cx="49" cy="49" r="49" fill="#fbc486"/>
    <circle cx="49" cy="49" r="40" fill="#ef8a2a"/>
    <circle cx="49" cy="49" r="33" fill="#f2741c"/>
  </svg>

  <div class="copy copy-left copy-supported">
    <p>Students benefit from informed educational<br>leadership and policymaking that result<br>in effective career resources &amp;<br>learning opportunities.</p>
    <ul>
      <li>Professional Development</li>
      <li>Industry-Education<br>Relationships</li>
      <li>Federal CTE Technical<br>Support</li>
      <li>BLW Policy Tools</li>
    </ul>
  </div>

  <div class="copy copy-right copy-wise">
    <p>Students have insight into personal values<br>&amp; interests, as well as the economic<br>realities of the job market, that<br>supports informed career<br>decisions.</p>
    <ul>
      <li>Career Pathways</li>
      <li>Career Exploration</li>
      <li>EducatorCareer Guides</li>
    </ul>
  </div>

  <div class="copy copy-left copy-engaged">
    <p>Students are motivated<br>&amp; inspired to develop career<br>skills &amp; seek employment<br>opportunities that meet both<br>personal &amp; community needs.</p>
    <ul>
      <li>Career Awareness &amp; Exposure</li>
      <li>Purposeful Learning Connected to Careers</li>
    </ul>
  </div>

  <div class="copy copy-right copy-prepared">
    <p>Students have the necessary<br>foundational, technical, &amp; workplace<br>skills needed to support success in a<br>variety of careers.</p>
    <ul>
      <li>Career-Focused Curricula</li>
      <li>Math Assessments with Gradia<br>Career Database</li>
      <li class="note">(powered by the Gradia® Framework for Mathematics)</li>
    </ul>
  </div>

  <svg class="wheel" viewBox="0 0 1200 899" aria-hidden="true">
    <defs>
      <path id="arcSupported" d="M -190,0 A 190 190 0 0 1 0,-190"/>
      <path id="arcWise" d="M 0,-190 A 190 190 0 0 1 190,0"/>
      <path id="arcEngaged" d="M -222,0 A 222 222 0 0 0 0,222"/>
      <path id="arcPrepared" d="M 0,222 A 222 222 0 0 0 222,0"/>
    </defs>
    <g transform="translate(600,512)">
      <circle r="276" fill="var(--white)"/>
      <circle r="266" fill="none" stroke="var(--ring-grey)" stroke-width="1.5"/>

      <path d="M -254.8,-10 A 255 255 0 0 1 -10,-254.8 L -10,-156.7 A 157 157 0 0 0 -156.7,-10 Z" fill="var(--supported)"/>
      <path d="M 10,-254.8 A 255 255 0 0 1 254.8,-10 L 156.7,-10 A 157 157 0 0 0 10,-156.7 Z" fill="var(--wise)"/>
      <path d="M 254.8,10 A 255 255 0 0 1 10,254.8 L 10,156.7 A 157 157 0 0 0 156.7,10 Z" fill="var(--prepared)"/>
      <path d="M -10,254.8 A 255 255 0 0 1 -254.8,10 L -156.7,10 A 157 157 0 0 0 -10,156.7 Z" fill="var(--engaged)"/>

      <g stroke="var(--ring-grey)" stroke-width="1.5">
        <line x1="0" y1="-266" x2="0" y2="266"/>
        <line x1="-266" y1="0" x2="266" y2="0"/>
      </g>
      <circle r="152" fill="var(--white)" stroke="var(--ring-grey)" stroke-width="1.5"/>
      <circle r="140" fill="var(--white)" stroke="var(--hub-ring)" stroke-width="9"/>

      <g fill="var(--white)" stroke="#4a4a4a" stroke-width="1.5">
        <circle cx="0" cy="-266" r="5.5"/><circle cx="0" cy="266" r="5.5"/>
        <circle cx="-266" cy="0" r="5.5"/><circle cx="266" cy="0" r="5.5"/>
        <circle cx="0" cy="-152" r="5.5"/><circle cx="0" cy="152" r="5.5"/>
        <circle cx="-152" cy="0" r="5.5"/><circle cx="152" cy="0" r="5.5"/>
      </g>
      <g fill="#3a3a3a">
        <circle cx="0" cy="-203" r="1.8"/><circle cx="0" cy="-209" r="1.8"/><circle cx="0" cy="-215" r="1.8"/>
        <circle cx="0" cy="203" r="1.8"/><circle cx="0" cy="209" r="1.8"/><circle cx="0" cy="215" r="1.8"/>
        <circle cx="-203" cy="0" r="1.8"/><circle cx="-209" cy="0" r="1.8"/><circle cx="-215" cy="0" r="1.8"/>
        <circle cx="203" cy="0" r="1.8"/><circle cx="209" cy="0" r="1.8"/><circle cx="215" cy="0" r="1.8"/>
      </g>
      <g fill="#777">
        <polygon points="-190,-183 -180,-189 -184,-178"/>
        <polygon points="190,-183 180,-189 184,-178"/>
        <polygon points="190,183 180,189 184,178"/>
        <polygon points="-190,183 -180,189 -184,178"/>
      </g>

      <text class="ring-label"><textPath href="#arcSupported" startOffset="50%" text-anchor="middle">CAREER SUPPORTED</textPath></text>
      <text class="ring-label"><textPath href="#arcWise" startOffset="50%" text-anchor="middle">CAREER WISE</textPath></text>
      <text class="ring-label"><textPath href="#arcEngaged" startOffset="50%" text-anchor="middle">CAREER ENGAGED</textPath></text>
      <text class="ring-label"><textPath href="#arcPrepared" startOffset="50%" text-anchor="middle">CAREER PREPARED</textPath></text>
    </g>
  </svg>

  <div class="hub">
    <div class="hub-heading">DATA-INFORMED &amp;<br>EVIDENCE-BASED PRACTICES</div>
    <div class="hub-body">Brightlane Work relies on robust labor<br>market data tools and sound educational<br>research to guide our development efforts and<br>encourage the use of informed career readiness<br>practices in educational settings.</div>
    <div class="hub-rule"></div>
    <div class="hub-heading">BLW DATA TOOLS</div>
    <ul class="hub-tools">
      <li>Labor Market Data System</li>
      <li>Employer Surveys</li>
      <li>Regional Labor Market Reports</li>
    </ul>
  </div>

  <div class="rule rule-bottom"></div>
</main>
</body>
</html>
```